Business card - KT Placement Partners / The Danford Group

We need a business card and logo design for my executive search (recruiting / headhunting) firm. We find people to fill open jobs at companies. We are a U.S. based company and do some global work also. So maybe something with a globe but definitely looking for other options also. Maybe something incorporating the letters KT which is our current logo but looking at options. The card should say BOTH full company names and tag line-

KT Placement Partners / The Danford Group
Executive Search Results You Can Count On

The design should say about the company-
Sharp
Reliable
Find the best people for the job
Business oriented
Results achieved
Modern

Target Market(s)

Business owners, CEO's, and heads of human resources departments

Industry/Entity Type

Business Consultant

Contact Information for Business Card

The card MUST say BOTH full company names and tag line-

Logo Text

Logo does not NEED to say anything on the design itself, but could if designed that way.

Font styles to use
Serif
Sans Serif

Requirements
Must have
• The business cards need to have. In addition to name, title, address, phone, website, and email address,
• The card MUST say BOTH full company names and tag line-
• KT Placement Partners / The Danford Group
• Executive Search Results You Can Count On
Nice to have
• The design should say about the company-
• Sharp
• Reliable
• Find the best people for the job
• Business oriented
• Results achieved
• Modern
• Maybe something with a globe or the letters KT or relating to people. Open to options.
Should not have
• Should not be cutesy or funny, for this design

```html
<!DOCTYPE html>
<html lang="en">
<head>
<meta charset="utf-8">
<title>KT Placement Partners / The Danford Group – Business Card</title>
<link rel="stylesheet" href="https://fonts.googleapis.com/css2?family=EB+Garamond:wght@400;600;700&family=Montserrat:wght@300;400;600;700&family=Playfair+Display:wght@400;500&display=swap">
<style>
  :root {
    --navy: #0e3a6b;
    --navy-deep: #0a2a52;
    --navy-shade: #082140;
    --paper: #f6f7f8;
    --ink: #2e3338;
    --grey: #5a6068;
    --stage: #e4e6e9;
    --white: #ffffff;
  }
  * { box-sizing: border-box; margin: 0; padding: 0; }
  html, body { width: 1200px; height: 873px; overflow: hidden; }
  body { background: var(--stage); position: relative; font-family: "EB Garamond", serif; }

  .card {
    position: absolute;
    width: 620px;
    height: 354px;
    box-shadow: 0 10px 30px rgba(0,0,0,.18);
    overflow: hidden;
  }

  /* Back side */
  .card--back { left: 70px; top: 60px; background: var(--navy); }
  .card--back .texture {
    position: absolute; inset: 0;
    background: linear-gradient(135deg, #134379 0%, var(--navy) 45%, var(--navy-deep) 100%);
  }
  .back-mark {
    position: absolute; left: 48px; top: 168px;
    font-family: "Playfair Display", serif; font-weight: 500;
    font-size: 120px; line-height: 1; color: var(--white); letter-spacing: -2px;
  }
  .tagline {
    position: absolute; left: 50px; top: 300px;
    font-family: "Montserrat", sans-serif; font-weight: 600;
    font-size: 15px; letter-spacing: 1.6px; color: var(--navy-shade);
  }

  /* Front side */
  .card--front { left: 510px; top: 450px; background: var(--paper); }
  .brand { position: absolute; left: 34px; top: 44px; display: flex; align-items: center; }
  .brand-mark {
    font-family: "Playfair Display", serif; font-weight: 500;
    font-size: 62px; line-height: 1; color: var(--navy); letter-spacing: -1px;
  }
  .brand-divider { width: 2px; height: 64px; background: var(--ink); margin: 0 12px 0 12px; }
  .brand-names { display: flex; flex-direction: column; gap: 2px; }
  .brand-primary { font-family: "Montserrat", sans-serif; font-weight: 300; font-size: 23px; color: var(--grey); }
  .brand-secondary { font-family: "Montserrat", sans-serif; font-weight: 700; font-size: 18px; letter-spacing: 3.5px; color: var(--navy); text-transform: uppercase; }

  .contact-list { position: absolute; left: 38px; top: 168px; list-style: none; }
  .contact-list li { display: flex; align-items: center; gap: 14px; height: 27px; font-size: 17px; color: var(--ink); }
  .contact-list svg { width: 17px; height: 17px; fill: var(--navy); flex: none; }

  .column-rule { position: absolute; left: 354px; top: 128px; }

  .person { position: absolute; left: 392px; top: 120px; }
  .person-name { font-weight: 700; font-size: 20px; color: var(--navy); }
  .person-title { font-size: 15px; color: var(--ink); margin-top: 1px; }
  .person-address { margin-top: 30px; font-size: 17px; line-height: 1.3; color: var(--navy); }

  .web-band {
    position: absolute; left: 0; right: 0; bottom: 0; height: 60px;
    background: var(--navy);
    display: flex; align-items: center; justify-content: center;
    font-weight: 600; font-size: 18px; letter-spacing: 2.5px; color: var(--white);
  }
</style>
</head>
<body>

  <section class="card card--back" aria-label="Card back">
    <div class="texture" role="img" aria-label="Faint navy faceted background texture"></div>
    <div class="back-mark">KT</div>
    <p class="tagline">Executive Search Results You Can Count On</p>
  </section>

  <section class="card card--front" aria-label="Card front">
    <div class="brand">
      <span class="brand-mark">KT</span>
      <span class="brand-divider"></span>
      <div class="brand-names">
        <span class="brand-primary">KT Placement Partners</span>
        <span class="brand-secondary">The Danford Group</span>
      </div>
    </div>

    <ul class="contact-list">
      <li><svg viewBox="0 0 24 24" aria-hidden="true"><path d="M3 9c0-2 4-4 9-4s9 2 9 4v2h-5V9c-1-.6-2.4-1-4-1s-3 .4-4 1v2H3zM6 12h12l2 7H4z"/></svg>555-214-3380</li>
      <li><svg viewBox="0 0 24 24" aria-hidden="true"><path d="M7 3h10v5H7zM4 9h16v8h-3v4H7v-4H4zm5 6v4h6v-4z"/></svg>555-214-3382</li>
      <li><svg viewBox="0 0 24 24" aria-hidden="true"><path d="M3 5h18v14H3zm2 2v.5l7 5 7-5V7zm0 3v7h14v-7l-7 5z"/></svg>dan@danfordgroup.com</li>
      <li><svg viewBox="0 0 24 24" aria-hidden="true"><path d="M10 14l4-4 1.4 1.4-4 4zM7 13l-2 2a3 3 0 004 4l2-2 1.4 1.4-2 2a5 5 0 01-7-7l2-2zm10-2l2-2a3 3 0 00-4-4l-2 2-1.4-1.4 2-2a5 5 0 017 7l-2 2z"/></svg>www.danfordgroup.com</li>
    </ul>

    <svg class="column-rule" width="20" height="130" viewBox="0 0 20 130" aria-hidden="true">
      <defs>
        <linearGradient id="rule-fade" x1="0" y1="0" x2="0" y2="1">
          <stop offset="0" stop-color="#0e3a6b" stop-opacity=".15"/>
          <stop offset=".5" stop-color="#0e3a6b"/>
          <stop offset="1" stop-color="#0e3a6b" stop-opacity=".15"/>
        </linearGradient>
      </defs>
      <line x1="4" y1="2" x2="16" y2="128" stroke="url(#rule-fade)" stroke-width="3"/>
    </svg>

    <div class="person">
      <p class="person-name">Daniel Hargrove</p>
      <p class="person-title">Chief Operating Officer</p>
      <p class="person-address">48 Alder Lane,<br>Brookfield, PA 15021</p>
    </div>

    <div class="web-band">www.ktplacement.com</div>
  </section>

</body>
</html>
```